Community-based social network needs a new landing page

We need a landing page for a local social network in Singapore called "LaneKindred.sg". It is a website that help neighbours to connect with each other for mutual benefits such as providing professional/non-professional services, sharing items, and neighbourly help, etc.

There is an existing website but we want to completely revamp it. It is most important that the new landing page communicates that the neighbourhood has skills and services for people to discover.

The final design of the landing page should be modern, and communicates a sense of community and vibrancy. As a matter of priority, more real estate should be accorded to the neighbours providing services elements.

We have drafted 2 reference sites that communicates the key ideas/user propositions for your easy reference:
http://tarvelquin8.example-sites.com/lanekindred
http://tarvelquin8.example-sites.com/lanekindred2

As long as the key ideas/user propositions are kept to, we are open to any design proposals. I.e. you do not have to follow the design layout of the reference sites

Target Market(s)

Our target market is primarily the Singapore community, includes all genders, education levels and occupations, aged between 17-45 years old.

In the file uploaded, you will find pictures of Singapore neighbourhoods and people of local ethnicities. Please use them, but you may arrange and add further filters to better enhance them

Industry/Entity Type

Real Estate

Requirements
Nice to have
• Landing page could be similar to that of www.gatherloft.com, not just at the top, but also the way the other categories are presented at the bottom.

```html
<!DOCTYPE html>
<html lang="en">
<head>
<meta charset="utf-8">
<title>LaneKindred.sg — Find people living near you</title>
<link href="https://fonts.googleapis.com/css2?family=Arvo&family=Raleway:wght@400;500;600&display=swap" rel="stylesheet">
<style>
:root{
  --red:#d0141b;
  --red-btn:#f2494b;
  --blue-link:#3d6cb0;
  --gold:#d9a10c;
  --ink:#333;
  --muted:#8a8a8a;
  --panel:#f3f3f3;
  --page:#e9e9e9;
  --footer:#2b2b2b;
  --rule:#d6d6d6;
}
*{box-sizing:border-box;margin:0;padding:0}
html,body{width:1093px;height:1200px;overflow:hidden}
body{position:relative;background:var(--page);font-family:"Raleway",Arial,sans-serif;color:var(--ink)}
.abs{position:absolute}
.hero{left:0;top:0;width:1093px;height:620px;background:linear-gradient(180deg,#d8cdea 0%,#7d86c4 30%,#5b6db0 55%,#c49a8a 78%,#6a7fb0 100%)}
.topbar{left:0;top:0;width:1093px;height:81px;background:rgba(238,234,250,.88);box-shadow:0 2px 6px rgba(0,0,0,.25)}
.brand{left:100px;top:24px;display:flex;align-items:center;gap:8px;font-size:27px;font-weight:600;color:#444;letter-spacing:-.5px}
.brand-dot{width:20px;height:20px;background:#f0c31c;border-radius:50%}
.btn{top:24px;width:90px;height:28px;font-size:16px;color:#fff;display:flex;align-items:center;justify-content:center;border-radius:2px}
.btn-signup{left:705px;background:var(--red-btn);border:1px solid #c22}
.btn-login{left:804px;background:#151515}
.btn-social{left:903px;background:#1c5fb0}
.story{height:83px;background:rgba(240,240,250,.82);border-radius:3px;font-size:14px;color:#666;line-height:18px}
.story h3{font-size:16px;font-weight:500;color:#333;margin-bottom:6px}
.story-a{left:210px;top:173px;width:443px;padding:12px 20px 0 36px}
.story-b{left:441px;top:318px;width:439px;padding:12px 40px 0 23px}
.avatar{width:128px;height:128px;border-radius:50%;border:2px solid #fff;background:radial-gradient(circle at 50% 45%,#d9b49c,#5a3a32)}
.panel{left:100px;top:469px;width:893px;height:598px;background:var(--panel)}
.headline{left:100px;top:480px;width:893px;text-align:center;font-family:"Arvo",Georgia,serif;font-size:25px;color:#444}
.headline em{font-style:normal;color:var(--blue-link)}
.intro{left:160px;top:522px;width:773px;text-align:center;font-size:14px;line-height:18px;color:#888}
.feature{width:262px;text-align:center}
.feature h2{font-family:"Arvo",Georgia,serif;font-weight:400;font-size:19px;color:var(--red);margin:6px 0 6px}
.feature p{font-size:12px;line-height:16.5px;color:#999}
.section-title{font-size:18px;font-weight:500;color:#444;display:flex;align-items:center;gap:8px}
.section-title::after{content:"";flex:1;border-top:3px double var(--rule)}
.listing{left:117px;width:263px}
.item{display:flex;gap:14px;border-bottom:1px solid #ddd;padding:6px 0 6px}
.item svg{flex:none;margin-top:4px}
.item h4{font-size:15.5px;font-weight:500;color:var(--gold)}
.item p{font-size:10.5px;line-height:13px;color:#888;margin-top:3px}
.users{left:416px;top:801px;display:grid;grid-template-columns:repeat(4,53px);gap:11px 16px}
.thumb{width:53px;height:51px}
.media{left:712px;width:263px;font-size:10.5px;line-height:13.5px;color:#888}
.plug{display:inline-flex;align-items:center;gap:3px;font-size:10.5px;color:#333;border:1px solid #bbb;border-radius:2px;padding:2px 4px;background:#fff}
.count{font-size:10px;border:1px solid #bbb;padding:2px 4px;background:#fff;margin-left:4px}
.sq{width:28px;height:28px;border-radius:4px;display:inline-block;margin-right:2px}
.footer{left:100px;top:1067px;width:893px;height:133px;background:var(--footer);color:#eee}
.footer .copy{left:18px;top:25px;font-size:14px}
.footer .quote{left:18px;top:53px;width:420px;font-size:10.5px;line-height:13.5px;color:#ddd}
.fcol{top:25px;font-size:10.5px;line-height:16.5px;color:#ddd}
.fcol h5{font-size:14px;font-weight:600;color:#eee;margin-bottom:9px}
</style>
</head>
<body>

<div class="abs hero" role="img" aria-label="Singapore waterfront skyline at dusk with towers and lit bay"></div>

<header class="abs topbar"></header>
<div class="abs brand"><span class="brand-dot"></span>LaneKindred.sg</div>
<a class="abs btn btn-signup">Sign Up</a>
<a class="abs btn btn-login">Login</a>
<a class="abs btn btn-social">Login</a>

<div class="abs story story-a"><h3>Guitar Enthusiast</h3>Aisha, a non-professional guitar enthusiast, will teach beginner guitar for only $5 per lesson</div>
<div class="abs avatar" style="left:99px;top:150px" role="img" aria-label="Portrait photo of a neighbour offering guitar lessons"></div>

<div class="abs story story-b"><h3>Architecture</h3>Mei Ling, an architecture undergraduate, will design your home from only $200</div>
<div class="abs avatar" style="left:867px;top:296px" role="img" aria-label="Portrait photo of a neighbour offering architecture design"></div>

<main class="abs panel"></main>
<h1 class="abs headline" style="font-weight:400">Find people living near you for <em>useful things</em> &amp; <em>neighbourly</em> help</h1>
<p class="abs intro">Sed ut perspiciatis unde omnis iste natus error sit voluptatem accusantium doloremque laudantium, totam rem aperiam, eaque ipsa quae ab illo inventore veritatis et quasi architecto beatae vitae dicta sunt explicabo nemo enim ipsam voluptatem quia voluptas sit aspernatur aut odit aut fugit...</p>

<div class="abs feature" style="left:118px;top:602px">
  <svg width="46" height="50" viewBox="0 0 46 50"><circle cx="23" cy="13" r="11" fill="var(--red)"/><path d="M2 50 Q4 29 23 28 Q42 29 44 50Z" fill="var(--red)"/><path d="M20 30h6l-3 14z" fill="#fff"/></svg>
  <h2>Professional</h2>
  <p>Lorem ipsum dolor sit amet, consectetur adipisicing elit, sed do eiusmod tempor incididunt ut labore et dolore magna aliqua...</p>
</div>
<div class="abs feature" style="left:416px;top:602px">
  <svg width="50" height="50" viewBox="0 0 50 50"><path d="M12 14 Q12 2 25 2 Q38 2 38 14Z" fill="var(--red)"/><circle cx="25" cy="18" r="10" fill="none" stroke="var(--red)" stroke-width="3"/><path d="M3 50 Q5 31 25 30 Q45 31 47 50Z" fill="none" stroke="var(--red)" stroke-width="3"/><rect x="15" y="38" width="20" height="12" fill="var(--red)"/></svg>
  <h2>Non-Professional</h2>
  <p>Lorem ipsum dolor sit amet, consectetur adipisicing elit, sed do eiusmod tempor incididunt ut labore et dolore magna aliqua...</p>
</div>
<div class="abs feature" style="left:713px;top:602px">
  <svg width="52" height="52" viewBox="0 0 52 52"><g fill="var(--red)"><circle cx="40" cy="10" r="9"/><circle cx="11" cy="26" r="10"/><circle cx="40" cy="42" r="9"/></g><path d="M40 10 11 26 40 42" fill="none" stroke="var(--red)" stroke-width="6"/></svg>
  <h2>Share And Help</h2>
  <p>Lorem ipsum dolor sit amet, consectetur adipisicing elit, sed do eiusmod tempor incididunt ut labore et dolore magna aliqua...</p>
</div>

<section class="abs listing" style="top:762px">
  <h3 class="section-title">Latest Listing</h3>
  <div style="margin-top:10px">
    <div class="item"><svg width="40" height="30" viewBox="0 0 40 30"><rect x="16" y="8" width="16" height="18" rx="2" fill="var(--gold)"/><path d="M16 14 2 4" stroke="var(--gold)" stroke-width="3"/><path d="M32 10q8 4 0 12" fill="none" stroke="var(--gold)" stroke-width="2"/></svg><div><h4>Water Plants While Away</h4><p>Ben Tan wants to offer I can help water your plants while you're overseas! I'm dependable and detailed..</p></div></div>
    <div class="item"><svg width="40" height="36" viewBox="0 0 40 36"><path d="M24 0 10 20h9l-5 16 16-22h-9z" fill="var(--gold)"/></svg><div><h4>Electricity Repair (DIY)</h4><p>JKT wants to offer Electrical Repair (DIY)</p></div></div>
    <div class="item"><svg width="40" height="32" viewBox="0 0 40 32"><rect x="2" y="4" width="26" height="10" rx="2" fill="var(--gold)"/><rect x="28" y="7" width="8" height="3" fill="var(--gold)"/><rect x="6" y="14" width="8" height="16" rx="2" fill="var(--gold)"/></svg><div><h4>Driling</h4><p>RafiqS has shared Electric Drill</p></div></div>
    <div class="item" style="border-bottom-color:#ccc"><svg width="40" height="32" viewBox="0 0 40 32"><rect x="4" y="8" width="11" height="22" rx="3" fill="var(--gold)" transform="rotate(-20 10 19)"/><rect x="22" y="6" width="11" height="22" rx="3" fill="var(--gold)" transform="rotate(25 27 17)"/></svg><div><h4>Travel Accessories</h4><p>KelvinL is selling Micro/Nano Sim Adapters</p></div></div>
  </div>
</section>

<h3 class="abs section-title" style="left:414px;top:762px;width:264px">Latest Registered Users</h3>
<div class="abs users" role="img" aria-label="Grid of sixteen member profile photos">
  <div class="thumb" style="background:#3a4f8a"></div><div class="thumb" style="background:#2b2230"></div><div class="thumb" style="background:#8fa5b5"></div><div class="thumb" style="background:#a58a6e"></div>
  <div class="thumb" style="background:#c08a4a"></div><div class="thumb" style="background:#b6a79a"></div><div class="thumb" style="background:#7aa3d6"></div><div class="thumb" style="background:#b0463a"></div>
  <div class="thumb" style="background:#e7b54a"></div><div class="thumb" style="background:#6e7b5a"></div><div class="thumb" style="background:#4a9aa0"></div><div class="thumb" style="background:#cfcac4"></div>
  <div class="thumb" style="background:#5aa6cf"></div><div class="thumb" style="background:#9a8075"></div><div class="thumb" style="background:#6b4a42"></div><div class="thumb" style="background:#8f8a83"></div>
</div>

<section class="abs media" style="top:762px">
  <h3 class="section-title">Media Mention</h3>
  <p style="margin-top:16px">LaneKindred.sg is an initiative supported by KCNF.</p>
  <p style="margin-top:13px">“LaneKindred.sg fills a critical gap, by providing a mechanism for neighbours to communicate with each other their resources and their willingness to help.”<br>- NMP Darren Koh, CEO of KCNF</p>
  <h3 class="section-title" style="margin-top:14px">Follow Us</h3>
  <div style="margin-top:11px;display:flex;gap:6px;color:#333;font-size:10px"><span class="plug">Like</span><span style="width:130px">Be the first of your friends to like this.</span></div>
  <div style="margin-top:6px"><span class="plug">Post</span><span class="count">0</span></div>
  <div style="margin-top:8px"><span class="plug">Follow @kindred</span><span class="count">169K followers</span></div>
  <div style="margin-top:8px"><span class="sq" style="background:#3b5998"></span><span class="sq" style="background:#33b5e5"></span><span class="sq" style="background:#e0412f"></span></div>
</section>

<footer class="abs footer">
  <div class="abs copy">© Harbourleaf Pte LTD 2013</div>
  <div class="abs quote">LaneKindred.sg is an initiative supported by KCNF.<br><br>“LaneKindred.sg fills a critical gap, by providing a mechanism for neighbours to communicate with each other their resources and their willingness to help.”<br>- NMP Darren Koh, CEO of KCNF</div>
  <div class="abs fcol" style="left:483px"><h5>Want to know more?</h5>About Us<br>FAQ</div>
  <div class="abs fcol" style="left:642px"><h5>Using Lane Kindred</h5>Terms of use<br>Privacy Policy</div>
  <div class="abs fcol" style="left:798px"><h5>Get in touch</h5>Contact Us<br>Circlebook</div>
</footer>

</body>
</html>
```